Marta's Dwellings website

We need a simple website for our property investment business in the UK. We basically need our contact details and brief description.We have the company logo already done (via ArtFlockly) so please use these:https://drive.google.com/drive/folders/1szJ3iRhelElZ40NIFT7w-c14MaY3Y_oV?usp=sharingYou could use some stock photos of UK houses for now.Let me know when to provide more detailed descriptions, etc

Coding

Coded - Design and coding required

Number of Pages Required

1 page

Colors

Designer to choose colors to be used in the design.

```html
<!DOCTYPE html>
<html lang="en">
<head>
<meta charset="utf-8">
<title>Marta's Dwellings</title>
<link href="https://fonts.googleapis.com/css2?family=Montserrat:wght@400;500;600;700&family=Noto+Serif:ital@1&family=Roboto+Slab:wght@300;400&display=swap" rel="stylesheet">
<style>
:root{
  --ink:#222222;
  --muted:#6f6f6f;
  --grey:#7a7a7a;
  --btn:#808080;
  --soft:#f7f7f7;
  --white:#ffffff;
  --hero-top:#5c5c5c;
  --hero-bottom:#2a2a2a;
  --contact-edge:#151515;
  --field-hint:#c4c4c4;
}
*{margin:0;padding:0;box-sizing:border-box}
html,body{width:1200px;height:3483px;overflow:hidden;background:var(--white)}
body{position:relative;font-family:"Roboto Slab",serif;color:var(--ink)}
.abs{position:absolute}
.heading{font-family:"Montserrat",sans-serif;font-weight:700;text-transform:uppercase;text-align:center;color:var(--ink)}
.section-title{left:0;width:1200px;font-size:34px;letter-spacing:.5px}
.section-sub{left:0;width:1200px;text-align:center;font-family:"Noto Serif",serif;font-style:italic;font-size:14px;color:var(--muted)}

/* hero */
.hero{left:40px;top:44px;width:1128px;height:552px;background:linear-gradient(180deg,var(--hero-top) 0%,#4a4a4a 45%,var(--hero-bottom) 100%)}
.brand{left:100px;top:27px;width:125px;height:65px;background:rgba(70,70,70,.55);box-shadow:0 2px 6px rgba(0,0,0,.35);display:flex;align-items:center;justify-content:center;gap:6px}
.brand-mark{width:12px;height:12px;background:var(--white)}
.brand-name{font-family:"Montserrat",sans-serif;font-weight:600;font-size:11px;color:var(--white);white-space:nowrap}
.nav{right:112px;top:52px;display:flex;gap:25px}
.nav a{font-family:"Montserrat",sans-serif;font-weight:600;font-size:12px;letter-spacing:1px;color:var(--white);text-decoration:none;text-transform:uppercase}
.hero-kicker{left:0;width:1128px;top:248px;text-align:center;font-family:"Noto Serif",serif;font-style:italic;font-size:34px;color:var(--white)}
.hero-title{left:0;width:1128px;top:306px;font-size:62px;color:var(--white);letter-spacing:1px}
.hero-actions{left:399px;top:414px;display:flex;gap:4px}
.btn{font-family:"Montserrat",sans-serif;font-weight:700;font-size:15px;color:var(--white);background:var(--btn);text-transform:uppercase;display:flex;align-items:center;justify-content:center;height:58px;border-radius:3px}

/* services */
.service{top:816px;width:316px;height:289px;background:var(--white);box-shadow:0 3px 10px rgba(0,0,0,.3);text-align:center}
.service-icon{width:134px;height:112px;border-radius:50%;background:var(--grey);margin:13px auto 0;display:flex;align-items:center;justify-content:center}
.service h3{font-family:"Montserrat",sans-serif;font-weight:600;font-size:20px;margin-top:16px;text-transform:uppercase}
.service p{font-size:14px;font-weight:300;line-height:25px;color:var(--muted);padding:0 22px;margin-top:12px}

/* portfolio */
.portfolio{left:33px;top:1193px;width:1128px;height:938px;background:var(--soft)}
.project{width:294px;height:285px;background:var(--white)}
.project-photo{height:192px;width:100%}
.project h4{font-family:"Montserrat",sans-serif;font-weight:600;font-size:20px;text-align:center;margin-top:21px}
.project span{display:block;text-align:center;font-family:"Noto Serif",serif;font-style:italic;font-size:13px;color:var(--muted);margin-top:3px}

/* about */
.about-photo{left:166px;top:2358px;width:371px;height:243px;background:linear-gradient(180deg,#cfcfcf,#6a6a6a 60%,#3a3a3a)}
.about-copy{left:608px;top:2361px;width:460px}
.about-copy p{font-size:14px;font-weight:300;line-height:25px;color:var(--muted);margin-bottom:13px}

/* contact */
.contact{left:33px;top:2699px;width:1128px;height:701px;background:var(--contact-edge)}
.contact-photo{left:28px;top:0;width:1072px;height:701px;background:linear-gradient(180deg,#616161 0%,#4a4a4a 40%,#2b2b2b 75%,#1c1c1c 100%)}
.contact-sub{left:0;width:1128px;top:151px;text-align:center;font-family:"Noto Serif",serif;font-style:italic;font-size:14px;color:#4e4e4e}
.info-card{top:242px;width:294px;height:72px;background:var(--white);border-radius:3px;text-align:center;overflow:hidden}
.info-card small{display:block;font-size:13px;margin-top:8px;color:var(--ink)}
.info-card strong{display:block;font-family:"Montserrat",sans-serif;font-weight:600;font-size:20px;margin-top:10px;white-space:nowrap}
.social{top:243px;width:41px;height:41px;border-radius:50%;background:#2a2a2a}
.field{width:452px;height:58px;background:var(--white);border-radius:3px;font-family:"Montserrat",sans-serif;font-size:13px;color:var(--field-hint);padding:18px 16px}
.message{left:577px;top:315px;width:451px;height:216px;background:var(--white);border-radius:3px;font-family:"Montserrat",sans-serif;font-size:13px;color:var(--field-hint);padding:18px 16px}
.send{left:467px;top:555px;width:193px}

/* footer */
.copyright{left:259px;top:3438px;font-family:"Montserrat",sans-serif;font-size:11px;color:var(--ink)}
.footer-links{left:667px;top:3443px;display:flex;gap:10px}
.footer-links a{font-family:"Montserrat",sans-serif;font-size:11px;color:var(--muted);text-decoration:none}
</style>
</head>
<body>

<header class="abs hero">
  <div class="abs" role="img" aria-label="Photo of a countryside cottage beside a pond with trees" style="inset:0;background:radial-gradient(ellipse at 50% 60%,rgba(120,120,120,.35),transparent 60%)"></div>
  <div class="abs brand"><span class="brand-mark"></span><span class="brand-name">Marta's Dwellings</span></div>
  <nav class="abs nav"><a href="#">About</a><a href="#">Services</a><a href="#">Projects</a><a href="#">Contact</a></nav>
  <p class="abs hero-kicker">Marta's Dwellings</p>
  <h1 class="abs heading hero-title">It's nice to meet you</h1>
  <div class="abs hero-actions">
    <a class="btn" style="width:150px">Projects</a>
    <a class="btn" style="width:175px">Learn More</a>
  </div>
</header>

<h2 class="abs heading section-title" style="top:678px">Services</h2>
<p class="abs section-sub" style="top:731px">Lorem ipsum dolor sit amet consectetur.</p>

<article class="abs service" style="left:120px">
  <div class="service-icon">
    <svg width="60" height="56" viewBox="0 0 60 56"><path d="M30 4 L4 28 H12 V52 H25 V36 H35 V52 H48 V28 H56 Z" fill="#fff"/></svg>
  </div>
  <h3>Service Type One</h3>
  <p>Lorem ipsum dolor sit amet, consectetur adipisicing elit. Minima maxime quam architecto quo inventore harum ex magni, dicta impedit.</p>
</article>
<article class="abs service" style="left:439px">
  <div class="service-icon">
    <svg width="44" height="60" viewBox="0 0 44 60"><rect x="4" y="2" width="36" height="56" fill="#fff"/><g fill="#7a7a7a"><rect x="12" y="10" width="6" height="6"/><rect x="26" y="10" width="6" height="6"/><rect x="12" y="22" width="6" height="6"/><rect x="26" y="22" width="6" height="6"/><rect x="12" y="34" width="6" height="6"/><rect x="26" y="34" width="6" height="6"/><rect x="18" y="46" width="8" height="12"/></g></svg>
  </div>
  <h3>Service Type Two</h3>
  <p>Lorem ipsum dolor sit amet, consectetur adipisicing elit. Minima maxime quam architecto quo inventore harum ex magni, dicta impedit.</p>
</article>
<article class="abs service" style="left:758px">
  <div class="service-icon">
    <svg width="66" height="50" viewBox="0 0 66 50"><path d="M2 48 V10 H18 V2 H40 V16 H64 V48 Z" fill="#fff"/><g fill="#7a7a7a"><rect x="8" y="18" width="5" height="5"/><rect x="8" y="30" width="5" height="5"/><rect x="24" y="10" width="5" height="5"/><rect x="32" y="10" width="5" height="5"/><rect x="24" y="22" width="5" height="5"/><rect x="32" y="22" width="5" height="5"/><rect x="24" y="34" width="5" height="5"/><rect x="32" y="34" width="5" height="5"/><rect x="46" y="24" width="5" height="5"/><rect x="54" y="24" width="5" height="5"/><rect x="46" y="36" width="5" height="5"/><rect x="54" y="36" width="5" height="5"/></g></svg>
  </div>
  <h3>Service Type Three</h3>
  <p>Lorem ipsum dolor sit amet, consectetur adipisicing elit. Minima maxime quam architecto quo inventore harum ex magni, dicta impedit.</p>
</article>

<section class="abs portfolio">
  <h2 class="abs heading section-title" style="left:-33px;top:89px">Portfolio</h2>
  <p class="abs section-sub" style="left:-33px;top:141px">Lorem ipsum dolor sit amet consectetur.</p>

  <div class="abs project" style="left:99px;top:226px"><div class="project-photo" role="img" aria-label="Photo of a modern apartment block with balconies" style="background:linear-gradient(160deg,#9a9a9a,#e0e0e0 40%,#555)"></div><h4>Project 1</h4><span>Category</span></div>
  <div class="abs project" style="left:417px;top:226px"><div class="project-photo" role="img" aria-label="Photo of a stately stone manor house" style="background:linear-gradient(180deg,#d8d8d8,#8a8a8a 55%,#5a5a5a)"></div><h4>Project 2</h4><span>Category</span></div>
  <div class="abs project" style="left:735px;top:226px"><div class="project-photo" role="img" aria-label="Photo of a cottage reflected in a pond" style="background:linear-gradient(180deg,#bcbcbc,#4e4e4e 55%,#2e2e2e)"></div><h4>Project 3</h4><span>Category</span></div>
  <div class="abs project" style="left:99px;top:539px"><div class="project-photo" role="img" aria-label="Photo of a thatched cottage" style="background:linear-gradient(180deg,#e6e6e6,#8c8c8c 55%,#4a4a4a)"></div><h4>Project 4</h4><span>Category</span></div>
  <div class="abs project" style="left:417px;top:539px"><div class="project-photo" role="img" aria-label="Photo of a cottage behind a wooden fence" style="background:linear-gradient(180deg,#6a6a6a,#9a9a9a 50%,#3c3c3c)"></div><h4>Project 5</h4><span>Category</span></div>
  <div class="abs project" style="left:735px;top:539px"><div class="project-photo" role="img" aria-label="Photo of a brick house behind a hedge" style="background:linear-gradient(180deg,#e4e4e4,#6a6a6a 50%,#3a3a3a)"></div><h4>Project 6</h4><span>Category</span></div>
</section>

<h2 class="abs heading section-title" style="top:2222px">About</h2>
<p class="abs section-sub" style="top:2274px">Lorem ipsum dolor sit amet consectetur.</p>
<div class="abs about-photo" role="img" aria-label="Photo of a brick house behind a hedge among trees"></div>
<div class="abs about-copy">
  <p>Lorem ipsum dolor sit amet, consectetur adipisicing elit. Minima maxime quam architecto quo inventore harum ex magni, dicta impedit.</p>
  <p>Lorem ipsum dolor sit amet, consectetur adipisicing elit. Minima maxime quam architecto quo inventore harum ex magni, dicta impedit.</p>
  <p>Lorem ipsum dolor sit amet, consectetur adipisicing elit. Minima maxime quam architecto quo inventore harum ex magni, dicta impedit.</p>
  <p>Lorem ipsum dolor sit amet, consectetur adipisicing elit. Minima maxime quam architecto quo inventore harum ex magni, dicta impedit.</p>
</div>

<section class="abs contact">
  <div class="abs contact-photo" role="img" aria-label="Dark photo of a cottage among trees reflected in a pond"></div>
  <h2 class="abs heading section-title" style="left:0;width:1128px;top:90px">Contact Us</h2>
  <p class="abs contact-sub">Lorem ipsum dolor sit amet consectetur.</p>

  <div class="abs info-card" style="left:99px"><small>Call Us</small><strong>+1 5550 1234 56</strong></div>
  <span class="abs social" style="left:490px" role="img" aria-label="Social profile link"></span>
  <span class="abs social" style="left:542px" role="img" aria-label="Social profile link"></span>
  <span class="abs social" style="left:594px" role="img" aria-label="Social profile link"></span>
  <div class="abs info-card" style="left:735px"><small>Mail Us</small><strong>mail@martahomes.com</strong></div>

  <div class="abs field" style="left:99px;top:315px">Your Name *</div>
  <div class="abs field" style="left:99px;top:394px">Your Email *</div>
  <div class="abs field" style="left:99px;top:474px">Your Phone *</div>
  <div class="abs message">Your Message *</div>
  <a class="abs btn send">Send Message</a>
</section>

<p class="abs copyright">Copyright © Marta's Dwellings 2019</p>
<nav class="abs footer-links"><a href="#">Privacy Policy</a><a href="#">Terms of Use</a><a href="#" style="margin-left:12px">About</a><a href="#" style="margin-left:22px">Projects</a></nav>

</body>
</html>
```